Every Shelf Set Neatly or ESN Organized needs a business card design. ESN Organized is a professi

We need a business card design that is clean, sharp and conveys a sense of organization. I already have a logo.

Target Market(s)

Families (specifically mothers), small business owners, parents, seniors

Industry/Entity Type

Business

Contact Information for Business Card

My website is www.esnorganized-example.com and my Facebook page is http://www.sociallink-example.com/everyshelfsetneatly. The phone number is 418-552-7094 and I want to be listed as Lorna M. Pelham, Owner

Requirements
Must have
• My logo.

```html
<!DOCTYPE html>
<html lang="en">
<head>
<meta charset="utf-8">
<title>Every Shelf Set Neatly – Business Card</title>
<link rel="stylesheet" href="https://fonts.googleapis.com/css2?family=Montserrat:wght@400;600&display=swap">
<style>
  :root {
    --stage: #262626;
    --brand-blue: #0a78d8;
    --panel-black: #111111;
    --paper-white: #f2f2f0;
    --ink-dark: #1b1b1b;
    --text-light: #ffffff;
  }
  * { margin: 0; padding: 0; box-sizing: border-box; }
  html, body {
    width: 1200px; height: 840px; overflow: hidden;
    background: var(--stage);
    font-family: "Montserrat", sans-serif;
  }
  .canvas { position: relative; width: 1200px; height: 840px; }
  .card { position: absolute; width: 459px; height: 262px; overflow: hidden; }
  .card--front { left: 451px; top: 121px; background: var(--brand-blue); color: var(--text-light); }
  .card--back { left: 318px; top: 442px; background: var(--paper-white); color: var(--ink-dark); }

  .brand-name {
    display: flex; align-items: center; gap: 9px;
    font-weight: 400; font-size: 20px; letter-spacing: 0.01em;
    white-space: nowrap;
  }
  .brand-name__mark { width: 11px; height: 11px; background: currentColor; flex: none; }
  .card--front .brand-name { position: absolute; left: 27px; top: 46px; }
  .card--back .brand-name {
    position: absolute; left: 0; right: 0; top: 121px; justify-content: center;
  }
  .card--back .brand-name__mark { background: var(--brand-blue); }

  .side-panel { position: absolute; left: 0; top: 0; }

  .contact { position: absolute; left: 27px; top: 142px; }
  .contact__name { font-weight: 600; font-size: 18px; line-height: 1.2; }
  .contact__role { font-size: 13.5px; line-height: 1.25; margin-bottom: 11px; }
  .contact__line { font-size: 12px; line-height: 17.5px; white-space: nowrap; }
  .contact__phone { font-weight: 600; }
  .contact__social { display: flex; align-items: center; gap: 5px; }
  .contact__social-box { width: 10px; height: 10px; background: var(--text-light); flex: none; }
</style>
</head>
<body>
<main class="canvas">
  <section class="card card--front" aria-label="Card front">
    <svg class="side-panel" width="459" height="262" viewBox="0 0 459 262" role="img" aria-label="Large paperclip illustration on a black band">
      <path d="M375 0 H459 V262 H312 C284 262 268 240 274 214 L348 60 Z" fill="var(--panel-black)"/>
    </svg>
    <div class="brand-name"><span class="brand-name__mark"></span>Every Shelf Set Neatly</div>
    <div class="contact">
      <p class="contact__name">Lorna M. Pelham</p>
      <p class="contact__role">Owner</p>
      <p class="contact__line contact__phone">P : 418-552-7094</p>
      <p class="contact__line">www.esnorganized-example.com</p>
      <p class="contact__line contact__social"><span class="contact__social-box"></span>/everyshelfsetneatly</p>
    </div>
  </section>

  <section class="card card--back" aria-label="Card back">
    <div class="brand-name"><span class="brand-name__mark"></span>Every Shelf Set Neatly</div>
  </section>
</main>
</body>
</html>
```